Catering Company Website Design

We are working with a bbq catering company in California called Ember Plank Catering.
Some sites to use for content/competitors and inspiration:
https://19parsnips.com
https://mbetrovandel.com
https://ridgefeastco.com
https://tinforkdenvale.com (client's favorite)
https://www.marvenasmokehut.com (client's favorite)
https://www.theopenkettlekitchen.com
Thank you for taking the time to consider designing a website for us. We are web developers based in Stockton, CA, USA. Most of our projects go through the same process. Understanding this process may help you win a project with us. We custom-code all of our websites in-house. We don’t have any requirements as to what tools you use for your design, but we prefer Figma files. For any design that we label as four-stars, we send it to the client for review. The client picks the final design they want us to use. Once we complete this process, we will continue to show additional clients all the four-star sites and purchase them later. Your designs will have multiple chances to sell. For better chances of success, we ask that you follow these guidelines.
IMAGES:
If you use any images or icons in the design, we ask that you have a link to the asset so we can purchase the image/icon. Most of the designs we submit do not have the customer’s images on them unless they have some great images. Be creative; show us the feeling you are trying to portray with your image choices. Use any royalty-free site you choose. We subscribe to Zelvio and mainly use their images, but we can purchase images outside of Zelvio.
PLEASE NOTE: we will not submit designs to clients with watermarks on the images.
FONTS:
We ask that you identify the fonts used in the design. This can be done in a message if you want. We typically use Google Fonts and Zelvio Fonts.
CONTENT:
We're always open to different content and ideas. We often submit designs with stock images so the client can see our vision. We typically take pictures after the website launch to use their images with our vision. Lorem Ipsum is fine for paragraphs, but we ask that you write the headers in correct English. We want to be able to show the vision and identify the sections of the website.
INSPIRATION:
We typically add a couple of links in the brief of websites we like to help you get started in your design.
REVISIONS:
We do not often ask for revisions of the designs unless we see something in the design that may not appeal to the client. If there are slight changes that we want to make, we do that in the development process.
FEEDBACK:
We rarely give feedback on designs during the design process. We are working on many website projects and do not have the time to provide feedback. We usually respond if your request is well thought out and asks specific questions, but a note asking “feedback, please” usually goes unanswered

```html
<!DOCTYPE html>
<html lang="en">
<head>
<meta charset="utf-8">
<title>Ember Plank Catering</title>
<link href="https://fonts.googleapis.com/css2?family=Josefin+Sans:wght@600;700&family=Lato:wght@400;700&display=swap" rel="stylesheet">
<style>
:root{
  --red:#c8191b;
  --brown:#3b0d05;
  --ink:#3a0a05;
  --text:#4a3a36;
  --white:#ffffff;
}
*{box-sizing:border-box;margin:0;padding:0}
html,body{width:1200px;height:3919px;overflow:hidden;background:var(--white)}
body{position:relative;font-family:'Lato',sans-serif;color:var(--text)}
.abs{position:absolute}
.head{font-family:'Josefin Sans',sans-serif;font-weight:700;letter-spacing:1px;color:var(--ink);text-transform:uppercase}
.head .accent{color:var(--red)}
.btn{position:absolute;display:flex;align-items:center;justify-content:center;background:var(--red);color:var(--white);font-weight:700;font-size:15px;border-radius:5px;text-decoration:none}
/* nav */
.nav{position:absolute;left:0;top:0;width:1200px;height:111px;background:var(--white);z-index:3}
.nav a{position:absolute;top:44px;font-size:15px;color:var(--ink);text-decoration:none}
.nav a.active{top:36px;left:96px;width:68px;height:37px;line-height:37px;text-align:center;background:var(--red);color:var(--white);border-radius:20px}
.logo-disc{position:absolute;left:430px;top:-103px;width:340px;height:340px;border-radius:50%;background:var(--white);z-index:3;display:flex;flex-direction:column;align-items:center;justify-content:flex-end;padding-bottom:58px}
.logo-mark{width:24px;height:24px;border-radius:50%;background:var(--red);margin-bottom:10px}
.logo-name{font-family:'Josefin Sans',sans-serif;font-weight:700;font-size:25px;color:var(--ink);text-transform:uppercase;letter-spacing:1px}
/* hero */
.hero{position:absolute;left:0;top:111px;width:1200px;height:599px;background:radial-gradient(ellipse at 50% 80%,#8a4a2a 0%,#5a2c18 35%,#2a1510 70%,#141010 100%)}
.hero-text{position:absolute;left:0;width:1200px;text-align:center;color:var(--white)}
.dots{position:absolute;display:flex;gap:6px}
.dots span{width:12px;height:12px;border-radius:50%;background:var(--white)}
.photo{position:absolute;border-radius:22px;overflow:hidden}
/* about */
.about p{position:absolute;left:675px;width:415px;font-size:15px;line-height:22.5px}
/* bbq */
.bbq{position:absolute;left:111px;top:1334px;width:976px;height:438px;border-radius:20px;background:radial-gradient(ellipse at 40% 30%,#6a2210 0%,#4a1208 50%,#340a04 100%)}
.bbq p{position:absolute;left:68px;top:172px;width:840px;text-align:center;color:var(--white);font-size:15px;line-height:22.3px}
/* menu cards */
.card{position:absolute;top:2044px;width:301px;height:362px;background:var(--brown);border-radius:6px;overflow:hidden;text-align:center;color:var(--white)}
.card .pic{position:absolute;left:0;top:0;width:301px;height:228px}
.price{position:absolute;left:196px;top:142px;width:80px;height:80px;border-radius:50%;background:var(--red);color:var(--white);font-size:28px;font-weight:700;display:flex;align-items:center;justify-content:center}
.card h3{position:absolute;top:246px;width:100%;font-size:23px;font-weight:700}
.card p{position:absolute;top:278px;left:12px;width:277px;font-size:14.5px;line-height:22.5px}
.arrow{position:absolute;top:2195px;width:38px;height:38px;border-radius:50%;background:var(--red)}
/* features */
.feature .icon{position:absolute;left:113px;width:66px;height:66px;border-radius:50%;background:var(--red)}
.feature h4{position:absolute;left:202px;font-size:21px;font-weight:400;color:var(--ink)}
.feature p{position:absolute;left:200px;width:360px;font-size:14.5px;line-height:20.5px}
/* testimonials */
.quote{position:absolute;top:3288px;width:56px;height:56px;border-radius:50%;background:var(--red)}
.tcol{position:absolute;top:3368px;width:305px;text-align:center;font-size:14.5px;line-height:22.5px}
.tname{position:absolute;top:3505px;width:305px;text-align:center;font-size:18px;letter-spacing:1.5px;color:var(--ink)}
/* footer */
.footer{position:absolute;left:0;top:3654px;width:1200px;height:265px;background:var(--brown)}
.footer .links a{position:absolute;top:64px;color:var(--white);font-size:15px;text-decoration:none}
.socials{position:absolute;left:0;top:118px;width:1200px;display:flex;justify-content:center;gap:26px}
.social{font-size:15px;color:var(--white);display:flex;align-items:center;gap:7px}
.social i{width:14px;height:14px;border-radius:50%;background:var(--white);display:block}
.rule{position:absolute;top:220px;height:1px;background:rgba(255,255,255,.35)}
.copy{position:absolute;top:212px;left:0;width:1200px;text-align:center;color:var(--white);font-size:13px}
</style>
</head>
<body>

<nav class="nav">
  <a class="active" href="#">Home</a>
  <a href="#" style="left:210px">About Us</a>
  <a href="#" style="left:333px">Catering</a>
  <a href="#" style="left:806px">Menu</a>
  <a href="#" style="left:905px">Gallery</a>
  <a href="#" style="left:1014px">Contact Us</a>
</nav>
<div class="logo-disc">
  <span class="logo-mark"></span>
  <span class="logo-name">Ember Plank</span>
</div>

<section class="hero" role="img" aria-label="Chef in black gloves slicing smoked brisket and pulled pork on a wooden board">
  <div class="hero-text" style="top:180px;font-size:27px">Welcome To</div>
  <div class="hero-text head" style="top:228px;font-size:52px;color:var(--white);letter-spacing:2px">Ember Plank Catering</div>
  <div class="hero-text" style="top:298px;font-size:17.5px;line-height:23px">Lorem ipsum dolor sit amet, consectetur adipiscing elit, sed do eiusmod<br>tempor incididunt ut labore et dolore magna aliqua.</div>
  <a class="btn" href="#" style="left:514px;top:365px;width:171px;height:41px">Book Catering</a>
  <div class="dots" style="left:576px;top:523px"><span></span><span></span><span></span></div>
</section>

<section class="about">
  <div class="photo" style="left:111px;top:797px;width:456px;height:449px;background:linear-gradient(135deg,#6b6660,#3a3532 55%,#1f1c1a)" role="img" aria-label="Server placing grilled meat onto a plate at a chafing dish buffet"></div>
  <h2 class="head abs" style="left:675px;top:808px;font-size:48px">About <span class="accent">Us</span></h2>
  <p style="top:890px">Lorem ipsum dolor sit amet, consectetur adipiscing elit, sed do eiusmod tempor incididunt ut labore et dolore magna aliqua. Ut enim ad minim veniam, quis nostrud exercitation ullamco laboris nisi ut aliquip ex ea commodo consequat.</p>
  <p style="top:1002px">Sed ut perspiciatis unde omnis iste natus error sit voluptatem accusantium doloremque laudantium, totam rem aperiam, eaque ipsa quae ab illo inventore veritatis et quasi architecto beatae vitae dicta sunt explicabo. Duis aute irure dolor in reprehenderit in voluptate velit esse cillum dolore eu fugiat nulla pariatur. Excepteur sint occaecat cupidatat non proi dent, sunt in culpa qui officia deserunt mollit&nbsp; laborum.</p>
  <a class="btn" href="#" style="left:675px;top:1203px;width:171px;height:43px">Read More</a>
</section>

<section class="bbq" role="img" aria-label="Dark close-up of smoked ribs on a grill">
  <h2 class="head abs" style="left:0;width:976px;text-align:center;top:86px;font-size:50px;color:var(--white)">Our BBQ</h2>
  <p>Lorem ipsum dolor sit amet, consectetur adipiscing elit, sed do eiusmod tempor incididunt ut labore et dolore magna aliqua. Ut enim ad minim veniam, quis nostrud exercitation ullamco laboris nisi ut aliquip ex ea commodo consequat. Duis aute irure dolor in reprehenderit in voluptate velit esse cillum dolore eu fugiat nulla pariatur. Excepteur sint occaecat cupidatat non proi-dent, sunt in culpa qui officia deserunt mollit anim id est laborum. Sed ut perspiciatis unde omnis iste natus error sit voluptatem accusantium doloremque laudantium, totam rem aperiam, eaque ipsa quae ab illo inventore veritatis et quasi architecto beatae vitae dicta sunt explicabo.</p>
  <a class="btn" href="#" style="left:403px;top:325px;width:171px;height:41px">Read More</a>
</section>

<section class="menu">
  <h2 class="head abs" style="left:0;width:1200px;text-align:center;top:1876px;font-size:48px">Popular <span class="accent">Menu</span></h2>
  <p class="abs" style="left:240px;top:1942px;width:720px;text-align:center;font-size:15.5px;line-height:22.5px">Lorem ipsum dolor sit amet, consectetur adipiscing elit, sed do eiusmod tempor incididunt ut labore et dolore magna aliqua. Quis ipsum suspendisse ultrices gravida. Risus commodo viverra maecenas accumsan lacus vel facilisis.</p>

  <div class="arrow" style="left:52px"><svg width="38" height="38"><path d="M22 12 L15 19 L22 26" stroke="#fff" stroke-width="3" fill="none"/></svg></div>
  <div class="arrow" style="left:1110px"><svg width="38" height="38"><path d="M16 12 L23 19 L16 26" stroke="#fff" stroke-width="3" fill="none"/></svg></div>

  <article class="card" style="left:111px">
    <div class="pic" role="img" aria-label="Grilled sausages and bratwurst on a tray" style="background:linear-gradient(160deg,#b84a30,#8a2e1a 50%,#c9a070)"></div>
    <div class="price">$ 35</div>
    <h3>Lorem ipsum dolor</h3>
    <p>Quis ipsum suspendisse ultrices gravida. Risus commodo viverra maecenas accumsan lacus vel facilisis.</p>
  </article>
  <article class="card" style="left:449px">
    <div class="pic" role="img" aria-label="Grilled shrimp plated with fresh greens" style="background:linear-gradient(160deg,#3a3636,#d8d4d0 55%,#e0a040)"></div>
    <div class="price">$ 25</div>
    <h3>Lorem ipsum dolor</h3>
    <p>Quis ipsum suspendisse ultrices gravida. Risus commodo viverra maecenas accumsan lacus vel facilisis.</p>
  </article>
  <article class="card" style="left:786px">
    <div class="pic" role="img" aria-label="Chicken and vegetable skewers with a yogurt dip" style="background:linear-gradient(160deg,#e8e6e0,#b8a070 50%,#7a8a40)"></div>
    <div class="price">$ 35</div>
    <h3>Lorem ipsum dolor</h3>
    <p>Quis ipsum suspendisse ultrices gravida. Risus commodo viverra maecenas accumsan lacus vel facilisis.</p>
  </article>
</section>

<section class="why">
  <h2 class="head abs" style="left:114px;top:2506px;font-size:48px">Why <span class="accent">Choose Us</span></h2>
  <p class="abs" style="left:112px;top:2584px;width:430px;font-size:15px;line-height:22.5px">Lorem ipsum dolor sit amet, consectetur adipiscing elit, sed do eiusmod tempor incididunt ut labore et dolore magna aliqua. Ut enim ad minim veniam, quis nostrud exercitation ullamco laboris nisi ut aliquip ex ea commodo consequat.</p>

  <div class="feature">
    <div class="icon" style="top:2694px"><svg width="66" height="66"><circle cx="33" cy="33" r="18" stroke="#fff" stroke-width="2" fill="none"/><circle cx="33" cy="33" r="11" stroke="#fff" stroke-width="1.5" fill="none"/></svg></div>
    <h4 style="top:2698px">Always Fresh Food</h4>
    <p style="top:2728px">Ut enim ad minim veniam, quis nostrud exercitation laboris nisi ut aliquip ex ea commodo consequat.</p>
  </div>
  <div class="feature">
    <div class="icon" style="top:2791px"><svg width="66" height="66"><path d="M22 30 a7 7 0 0 1 8-9 a7 7 0 0 1 12 2 a6 6 0 0 1 2 11 v10 h-22 v-10 a6 6 0 0 1 0-4z" stroke="#fff" stroke-width="2" fill="none"/><path d="M22 40 h22" stroke="#fff" stroke-width="2"/></svg></div>
    <h4 style="top:2795px">Best Cooking Chef</h4>
    <p style="top:2825px">Ut enim ad minim veniam, quis nostrud exercitation laboris nisi ut aliquip ex ea commodo consequat.</p>
  </div>
  <div class="feature">
    <div class="icon" style="top:2886px"><svg width="66" height="66"><rect x="22" y="19" width="22" height="28" rx="2" stroke="#fff" stroke-width="2" fill="none"/><path d="M27 26 h12 M27 32 h12 M27 38 h8" stroke="#fff" stroke-width="1.5"/></svg></div>
    <h4 style="top:2890px">100% Original Recipe</h4>
    <p style="top:2920px">Ut enim ad minim veniam, quis nostrud exercitation laboris nisi ut aliquip ex ea commodo consequat.</p>
  </div>

  <a class="btn" href="#" style="left:112px;top:3004px;width:171px;height:41px">Read More</a>
  <div class="photo" style="left:631px;top:2491px;width:456px;height:600px;background:radial-gradient(ellipse at 75% 55%,#f0a030 0%,#a05018 25%,#3a2a24 60%,#1a1614 100%)" role="img" aria-label="Chef cooking over flaming pans in a restaurant kitchen"></div>
</section>

<section class="testimonials">
  <h2 class="head abs" style="left:0;width:1200px;text-align:center;top:3199px;font-size:48px">Our <span class="accent">Testimonials</span></h2>

  <div class="quote" style="left:231px"><svg width="56" height="56"><path d="M20 22 h6 v7 q0 6-5 8 M31 22 h6 v7 q0 6-5 8" stroke="#fff" stroke-width="4" fill="none"/></svg></div>
  <div class="quote" style="left:573px"><svg width="56" height="56"><path d="M20 22 h6 v7 q0 6-5 8 M31 22 h6 v7 q0 6-5 8" stroke="#fff" stroke-width="4" fill="none"/></svg></div>
  <div class="quote" style="left:914px"><svg width="56" height="56"><path d="M20 22 h6 v7 q0 6-5 8 M31 22 h6 v7 q0 6-5 8" stroke="#fff" stroke-width="4" fill="none"/></svg></div>

  <p class="tcol" style="left:107px">Lorem ipsum dolor sit amet, consectetur adipiscing elit, sed do eiusmod tempor incididunt ut labore et dolore magna aliqua. Quis ipsum suspendisse ultrices gravida. Risus commodo viverra maecenas accumsan lacus vel facilisis.</p>
  <p class="tcol" style="left:448px">Lorem ipsum dolor sit amet, consectetur adipiscing elit, sed do eiusmod tempor incididunt ut labore et dolore magna aliqua. Quis ipsum suspendisse ultrices gravida. Risus commodo viverra maecenas accumsan lacus vel facilisis.</p>
  <p class="tcol" style="left:789px">Lorem ipsum dolor sit amet, consectetur adipiscing elit, sed do eiusmod tempor incididunt ut labore et dolore magna aliqua. Quis ipsum suspendisse ultrices gravida. Risus commodo viverra maecenas accumsan lacus vel facilisis.</p>
  <div class="tname" style="left:107px">LOREM IPSUM</div>
  <div class="tname" style="left:448px">LOREM IPSUM</div>
  <div class="tname" style="left:789px">LOREM IPSUM</div>

  <div class="dots" style="left:575px;top:3555px"><span style="background:var(--brown)"></span><span style="background:var(--red)"></span><span style="background:var(--red)"></span></div>
</section>

<footer class="footer">
  <div class="links">
    <a href="#" style="left:287px">Home</a>
    <a href="#" style="left:387px">About Us</a>
    <a href="#" style="left:510px">Catering</a>
    <a href="#" style="left:628px">Menu</a>
    <a href="#" style="left:727px">Gallery</a>
    <a href="#" style="left:836px">Contact Us</a>
  </div>
  <div class="socials">
    <span class="social"><i></i>Facelink</span>
    <span class="social"><i></i>Pictorama</span>
    <span class="social"><i></i>Chirp</span>
    <span class="social"><i></i>WorkNet</span>
  </div>
  <div class="rule" style="left:118px;width:290px"></div>
  <div class="rule" style="left:808px;width:290px"></div>
  <div class="copy">Copyright © 2024&nbsp; Ember Plank Catering. All rights reserved.</div>
</footer>

</body>
</html>
```